Bright Harbor website redesign

We need a redesign for a website: mybrightharbor.example.

I already created a video going over what exactly is needed in the design.

See Video here: https://files.example.net/file/d/7xQpL2mR9vTz4KwB8nYcH3jDs6FgA1eU0/view?usp=sharing

Google Slide shown in Video: https://slides.example.net/presentation/d/9KP_Rtnwq3XbzmLeYc7VhJ2GoUd4Fs_PaiTe6q1kQ5Wr/edit?usp=sharing

Holidays in India so we did not get enough design entries or quality.

Target Market(s)

Dentistry

Industry/Entity Type

Dentistry

Number of Pages Required

1 page

Colors
0094D4
00A9DD
6FCCEA
C7EBF8
E9F6FB
00AB8E
00BBA5
67D7C9
C6EFE9
E9F9F6

Requirements
Must have
• See 13 min video link in description - shows what to do.

```html
<!DOCTYPE html>
<html lang="en">
<head>
<meta charset="UTF-8">
<title>Bright Harbor – Page Header Options</title>
<link href="https://fonts.googleapis.com/css2?family=Poppins:wght@300;400;500;700&display=swap" rel="stylesheet">
<style>
  :root {
    --canvas: #ffffff;
    --title: #ffffff;
    --crumb-text: #111418;
    --crumb-bar: rgba(236, 238, 244, 0.82);
    --crumb-bar-blue: rgba(210, 230, 238, 0.85);
  }
  * { margin: 0; padding: 0; box-sizing: border-box; }
  html, body {
    width: 1200px;
    height: 1145px;
    overflow: hidden;
    background: var(--canvas);
    font-family: "Poppins", sans-serif;
  }
  .header-option {
    position: absolute;
    left: 24px;
    width: 1123px;
    height: 188px;
    overflow: hidden;
  }
  .header-option--one   { top: 40px; }
  .header-option--two   { top: 254px; }
  .header-option--three { top: 467px; }
  .header-option--four  { top: 681px; }
  .header-option--five  { top: 890px; }

  .header-photo {
    position: absolute;
    inset: 0;
  }
  .header-option--one .header-photo {
    background: linear-gradient(90deg, #8390ac 0%, #9a9bb4 30%, #b0a6b8 50%, #b39aa6 62%, #8f98b4 80%, #7d93c2 95%, #2f5fd0 100%);
  }
  .header-option--two .header-photo {
    background: linear-gradient(90deg, #7d665e 0%, #8a6f63 20%, #5e7a9c 32%, #6d7c93 45%, #8a6e60 62%, #a07e6c 78%, #8d8a8d 90%, #6e8f9a 100%);
  }
  .header-option--three .header-photo {
    background: linear-gradient(90deg, #5d6d91 0%, #6a7896 14%, #7c6a64 26%, #8c7568 34%, #7c7e88 48%, #8e9096 70%, #a5a4a8 85%, #7d8a86 100%);
  }
  .header-option--four .header-photo {
    background: linear-gradient(90deg, #626f7d 0%, #67737f 18%, #7c6a5c 30%, #957a68 42%, #a48775 58%, #8b7f7a 70%, #aaa4a1 82%, #b8b0ab 100%);
  }
  .header-option--five .header-photo {
    background: linear-gradient(90deg, #4a90ad 0%, #4a90ad 60%, #8fb3c6 70%, #c9d5df 78%, #a6c2d2 82%, #d3dde6 88%, #c6d2de 96%, #4a90ad 100%);
  }

  .header-title {
    position: absolute;
    left: 390px;
    top: 60px;
    color: var(--title);
    font-size: 37px;
    line-height: 48px;
    letter-spacing: 0.2px;
    white-space: nowrap;
  }
  .header-title .light { font-weight: 300; }
  .header-title .bold { font-weight: 700; }

  .breadcrumb {
    position: absolute;
    left: 0;
    right: 0;
    bottom: 0;
    height: 28px;
    background: var(--crumb-bar);
    display: flex;
    align-items: center;
    padding-left: 56px;
    font-size: 12px;
    color: var(--crumb-text);
    font-weight: 400;
    gap: 6px;
  }
  .breadcrumb--strong { font-weight: 500; }
  .header-option--five .breadcrumb { background: var(--crumb-bar-blue); }
  .breadcrumb svg { width: 10px; height: 8px; }
</style>
</head>
<body>

<section class="header-option header-option--one">
  <div class="header-photo" role="img" aria-label="Close-up photo of dental tools examining teeth models, tinted blue-grey"></div>
  <h1 class="header-title"><span class="light">Dental</span> <span class="bold">Implants</span></h1>
  <nav class="breadcrumb"><span>Home</span><svg viewBox="0 0 10 8"><path d="M1 1l3 3-3 3M5 1l3 3-3 3" fill="none" stroke="#111418" stroke-width="1.2"/></svg><span>Dental Implants</span></nav>
</section>

<section class="header-option header-option--two">
  <div class="header-photo" role="img" aria-label="Photo of a patient receiving a dental check-up from a gloved dentist"></div>
  <h1 class="header-title"><span class="light">Dental</span> <span class="bold">Implants</span></h1>
  <nav class="breadcrumb"><span>Home</span><svg viewBox="0 0 10 8"><path d="M1 1l3 3-3 3M5 1l3 3-3 3" fill="none" stroke="#111418" stroke-width="1.2"/></svg><span>Dental Implants</span></nav>
</section>

<section class="header-option header-option--three">
  <div class="header-photo" role="img" aria-label="Photo of a smiling patient in a dental chair beside a clinic sink"></div>
  <h1 class="header-title"><span class="light">Dental</span> <span class="bold">Implants</span></h1>
  <nav class="breadcrumb breadcrumb--strong"><span>Home</span><svg viewBox="0 0 10 8"><path d="M1 1l3 3-3 3M5 1l3 3-3 3" fill="none" stroke="#111418" stroke-width="1.4"/></svg><span>Dental Implants</span></nav>
</section>

<section class="header-option header-option--four">
  <div class="header-photo" role="img" aria-label="Photo of a smiling patient with a dentist holding an instrument"></div>
  <h1 class="header-title"><span class="light">Dental</span> <span class="bold">Implants</span></h1>
  <nav class="breadcrumb"><span>Home</span><svg viewBox="0 0 10 8"><path d="M1 1l3 3-3 3M5 1l3 3-3 3" fill="none" stroke="#111418" stroke-width="1.2"/></svg><span>Dental Implants</span></nav>
</section>

<section class="header-option header-option--five">
  <div class="header-photo" role="img" aria-label="Photo of dental floss container and a large tooth model on a blue background"></div>
  <h1 class="header-title"><span class="light">Dental</span> <span class="bold">Implants</span></h1>
  <nav class="breadcrumb breadcrumb--strong"><span>Home</span><svg viewBox="0 0 10 8"><path d="M1 1l3 3-3 3M5 1l3 3-3 3" fill="none" stroke="#111418" stroke-width="1.4"/></svg><span>Dental Implants</span></nav>
</section>

</body>
</html>
```